The book is called "Distance Racing Blueprints: An In-Depth Manual for Achieving Your Peak Race Day - Featuring Schedules, Counsel and Target-Reaching Pointers "

It is a 6" x 9" book with 205 pages. This is an advanced book for runners who have been running and trying to hit their marathon goals, but haven't been able to do so. This needs to portray a professional coaching image and high performing athlete.

I have running photos of myself running marathons if you thought that was the route to take, but I'm open to your creative influence.

```html
<!DOCTYPE html>
<html lang="en">
<head>
<meta charset="utf-8">
<title>Distance Racing Blueprints – Cover Wrap</title>
<link href="https://fonts.googleapis.com/css2?family=Jost:wght@400;500;600&family=Poppins:wght@500;600&family=Arimo:wght@400&display=swap" rel="stylesheet">
<style>
  :root {
    --stage: #2b2b2b;
    --paper: #ffffff;
    --ink: #111111;
    --red: #e3141f;
    --yellow: #f7bb1f;
    --coral: #ff6f5e;
  }
  * { margin: 0; padding: 0; box-sizing: border-box; }
  html, body { width: 1200px; height: 1200px; overflow: hidden; background: var(--stage); }

  .cover-wrap {
    position: absolute; left: 20px; top: 190px;
    width: 1160px; height: 819px;
    background: var(--paper);
    color: var(--ink);
  }

  /* Back cover */
  .back-title {
    position: absolute; left: 51px; top: 48px; width: 240px;
    font-family: "Jost", sans-serif; font-weight: 500;
    text-align: center; line-height: 0.98;
  }
  .back-title .line-1 { color: var(--red); font-size: 44px; display: block; }
  .back-title .line-2 { color: var(--yellow); font-size: 44px; display: block; }
  .back-title .line-3 { color: var(--ink); font-size: 32px; display: block; margin-top: 3px; }

  .back-subtitle {
    position: absolute; right: 662px; top: 60px; width: 200px;
    font-family: "Jost", sans-serif; font-weight: 500;
    font-size: 15px; line-height: 20px; text-align: right;
  }

  .back-blurb {
    position: absolute; left: 51px; top: 172px; width: 447px;
    font-family: "Arimo", sans-serif; font-size: 13.6px; line-height: 19px;
    text-align: justify;
  }
  .back-blurb p + p { margin-top: 19px; }

  /* Spine */
  .spine-text {
    position: absolute; left: 592px; top: 52px;
    transform-origin: 0 0; transform: rotate(90deg);
    font-family: "Jost", sans-serif; font-weight: 500;
    font-size: 30px; white-space: nowrap; line-height: 1;
  }
  .spine-text .word-red { color: var(--red); }
  .spine-text .word-yellow { color: var(--yellow); }
  .spine-author {
    position: absolute; left: 588px; top: 623px;
    transform-origin: 0 0; transform: rotate(90deg);
    font-family: "Jost", sans-serif; font-weight: 500;
    font-size: 18px; letter-spacing: 3px; white-space: nowrap;
  }

  /* Front cover */
  .front-title {
    position: absolute; left: 640px; top: 46px; width: 500px;
    font-family: "Jost", sans-serif; font-weight: 500;
    text-align: center; line-height: 1;
  }
  .front-title .line-1 { display: block; color: var(--red); font-size: 86px; }
  .front-title .line-2 { display: block; color: var(--yellow); font-size: 86px; margin-top: -6px; }
  .front-title .line-3 { display: block; color: var(--ink); font-size: 58px; margin-top: 2px; }

  .hero-photo {
    position: absolute; left: 648px; top: 262px; width: 476px; height: 420px;
    background:
      radial-gradient(ellipse 28% 45% at 50% 38%, rgba(255,111,94,0.55), transparent 70%),
      radial-gradient(ellipse 18% 30% at 78% 42%, rgba(247,187,31,0.45), transparent 70%),
      radial-gradient(ellipse 18% 30% at 20% 45%, rgba(255,111,94,0.35), transparent 70%),
      radial-gradient(ellipse 60% 28% at 50% 78%, rgba(40,40,40,0.18), transparent 70%),
      var(--paper);
  }

  .front-author {
    position: absolute; left: 664px; top: 750px;
    font-family: "Jost", sans-serif; font-weight: 500;
    font-size: 30px; letter-spacing: 4px; white-space: nowrap;
  }

  .seal-badge {
    position: absolute; left: 970px; top: 630px; width: 166px; height: 166px;
  }
  .seal-badge svg { position: absolute; inset: 0; width: 100%; height: 100%; }
  .seal-badge .seal-text {
    position: absolute; inset: 0;
    display: flex; align-items: center; justify-content: center;
    transform: rotate(-9deg);
    font-family: "Poppins", sans-serif; font-weight: 500;
    font-size: 10.5px; line-height: 12.5px; color: #fff; text-align: center;
  }
</style>
</head>
<body>
  <div class="cover-wrap">
    <!-- Back cover -->
    <h2 class="back-title">
      <span class="line-1">DISTANCE</span>
      <span class="line-2">RACING</span>
      <span class="line-3">BLUEPRINTS</span>
    </h2>
    <p class="back-subtitle">An In-Depth Manual for Achieving Your Peak Race Day - Featuring Schedules, Counsel and Target-Reaching Pointers</p>
    <div class="back-blurb">
      <p>Lorem ipsum dolor sit amet, consectetur adipiscing elit, sed do eiusmod tempor incididunt ut labore et dolore magna aliqua. Quis ipsum suspendisse ultrices gravida. Risus commodo viverra maecenas accumsan lacus vel facilisis. Lorem ipsum dolor sit amet, consectetur adipiscing elit, sed do eiusmod tempor incididunt ut labore et dolore magna aliqua. Quis ipsum suspendisse ultrices gravida. Risus commodo viverra maecenas accumsan lacus vel facilisis. Lorem ipsum dolor sit amet, consectetur adipiscing elit, sed do eiusmod tempor incididunt ut labore et dolore magna aliqua. Quis ipsum suspendisse ultrices gravida. Risus commodo viverra maecenas accumsan lacus vel facilisis. Lorem ipsum dolor sit amet, consectetur adipiscing elit, sed do eiusmod tempor incididunt ut labore et dolore magna aliqua. Quis ipsum suspendisse ultrices gravida. Risus commodo viverra maecenas accumsan lacus vel facilisis.</p>
      <p>Lorem ipsum dolor sit amet, consectetur adipiscing elit, sed do eiusmod tempor incididunt ut labore et dolore magna aliqua. Quis ipsum suspendisse ultrices gravida. Risus commodo viverra maecenas accumsan lacus vel facilisis. Lorem ipsum dolor sit amet, consectetur adipiscing elit, sed do eiusmod tempor incididunt ut labore et dolore magna aliqua. Quis ipsum suspendisse ultrices gravida. Risus commodo viverra maecenas accumsan lacus vel facilisis. Lorem ipsum dolor sit amet, consectetur adipiscing elit, sed do eiusmod tempor incididunt ut labore et dolore magna aliqua. Quis ipsum suspendisse ultrices gravida. Risus commodo viverra maecenas accumsan lacus vel facilisis.</p>
    </div>

    <!-- Spine -->
    <div class="spine-text"><span class="word-red">DISTANCE</span> <span class="word-yellow">RACING</span> BLUEPRINTS</div>
    <div class="spine-author">AUTHOR NAME</div>

    <!-- Front cover -->
    <h1 class="front-title">
      <span class="line-1">DISTANCE</span>
      <span class="line-2">RACING</span>
      <span class="line-3">BLUEPRINTS</span>
    </h1>
    <div class="hero-photo" role="img" aria-label="Photo of a group of runners in colourful sportswear, the lead runner breaking a red finish-line tape with arms raised"></div>
    <div class="front-author">AUTHOR NAME</div>

    <div class="seal-badge">
      <svg viewBox="-80 -80 160 160" aria-hidden="true">
        <polygon fill="var(--red)" transform="rotate(-9)" points="78,0 64.7,12.9 72.1,29.9 54.8,36.7 55.1,55.1 36.7,54.8 29.9,72.1 12.9,64.7 0,78 -12.9,64.7 -29.9,72.1 -36.7,54.8 -55.1,55.1 -54.8,36.7 -72.1,29.9 -64.7,12.9 -78,0 -64.7,-12.9 -72.1,-29.9 -54.8,-36.7 -55.1,-55.1 -36.7,-54.8 -29.9,-72.1 -12.9,-64.7 0,-78 12.9,-64.7 29.9,-72.1 36.7,-54.8 55.1,-55.1 54.8,-36.7 72.1,-29.9 64.7,-12.9"/>
      </svg>
      <div class="seal-text">An In-Depth<br>Manual for Achieving<br>Your Peak Race Day<br>Featuring Schedules,<br>Counsel and<br>Target-Reaching<br>Pointers</div>
    </div>
  </div>
</body>
</html>
```